Business Card Design Project

I would like a business card created for a new company. This is a holding company that acts as my investment company. It holds real estate and service based companies. The name of the company is Sorvantica which is Italian for Evolution. Defined as development or growth.
We currently have no logo. I really like some of the "different" cards out there. Potentially metallic or grey/black. That looks premium/hi-end and unique. I am not sure if your design would be specific to the card stock I end with our just logo/design/font.
Industry/Entity Type
Real Estate
Look and feel

```html
<!DOCTYPE html>
<html lang="en">
<head>
<meta charset="UTF-8">
<title>Sorvantica — Business Card</title>
<link rel="stylesheet" href="https://fonts.googleapis.com/css2?family=Noto+Sans:wght@400;700&display=swap">
<style>
  :root {
    --page: #1a2224;
    --card-frame: #8c9799;
    --band-top: #1c2629;
    --field-edge: #1f2b2e;
    --field-glow: #56686c;
    --band-bottom-light: #56676a;
    --band-bottom-dark: #34444a;
    --curve: #6d7e82;
    --wordmark: #c9d0d3;
    --heading: #d3dadc;
    --body-text: #c6ced1;
  }
  * { margin: 0; padding: 0; box-sizing: border-box; }
  html, body {
    width: 1200px;
    height: 683px;
    overflow: hidden;
    background: var(--page);
  }
  .card {
    position: relative;
    width: 1200px;
    height: 683px;
    overflow: hidden;
    border: 2px solid var(--card-frame);
  }
  .card-backdrop {
    position: absolute;
    inset: 0;
    width: 100%;
    height: 100%;
  }
  .card-content {
    position: absolute;
    inset: 0;
    text-align: center;
  }
  .wordmark {
    position: absolute;
    left: 0;
    right: 0;
    top: 200px;
    font-family: "Noto Sans", "Verdana", sans-serif;
    font-weight: 700;
    font-size: 128px;
    line-height: 1;
    letter-spacing: 1px;
    color: var(--wordmark);
    white-space: nowrap;
  }
  .tagline {
    position: absolute;
    left: 0;
    right: 0;
    top: 366px;
    font-family: "Noto Sans", "Verdana", sans-serif;
    font-weight: 700;
    font-size: 31px;
    line-height: 40px;
    color: var(--heading);
    white-space: nowrap;
  }
  .description {
    position: absolute;
    left: 0;
    right: 0;
    top: 407px;
    font-family: "Noto Sans", "Verdana", sans-serif;
    font-weight: 400;
    font-size: 28px;
    line-height: 41px;
    color: var(--body-text);
    white-space: nowrap;
  }
</style>
</head>
<body>
  <div class="card">
    <svg class="card-backdrop" viewBox="0 0 1196 679" preserveAspectRatio="none" aria-hidden="true">
      <defs>
        <radialGradient id="field-glow" cx="0.5" cy="0.58" r="0.62">
          <stop offset="0" stop-color="var(--field-glow)"/>
          <stop offset="0.55" stop-color="#34454a"/>
          <stop offset="1" stop-color="var(--field-edge)"/>
        </radialGradient>
        <linearGradient id="band-bottom" x1="0" y1="0" x2="0" y2="1">
          <stop offset="0" stop-color="var(--band-bottom-light)"/>
          <stop offset="0.35" stop-color="#4a5b5f"/>
          <stop offset="1" stop-color="var(--band-bottom-dark)"/>
        </linearGradient>
        <linearGradient id="band-top" x1="0" y1="0" x2="0" y2="1">
          <stop offset="0" stop-color="#2a3538"/>
          <stop offset="1" stop-color="var(--band-top)"/>
        </linearGradient>
      </defs>
      <rect class="field" x="0" y="0" width="1196" height="679" fill="url(#field-glow)"/>
      <rect class="band-top" x="0" y="0" width="1196" height="56" fill="url(#band-top)"/>
      <rect class="band-bottom" x="0" y="550" width="1196" height="129" fill="url(#band-bottom)"/>
      <line x1="0" y1="550" x2="1196" y2="550" stroke="#6f8084" stroke-width="2"/>
      <path class="band-curve" d="M0 625 C 220 560, 520 600, 760 650 S 1100 690, 1196 640" fill="none" stroke="var(--curve)" stroke-width="2" opacity="0.45"/>
    </svg>

    <div class="card-content">
      <h1 class="wordmark">Sorvantica</h1>
      <p class="tagline">Lorem ipsum dolor</p>
      <p class="description">sit amet, consectetur adipiscing elit. Aenean pellentesque ligula<br>sed risus pharetra ac porta neque aliquam. Cras ornare felis id<br>libero hendrerit fringilla.</p>
    </div>
  </div>
</body>
</html>
```